Stylish Business Cards Wanted

- DOUBLE SIDED Design Required -

High end, edgy cards for a corporate and personal stylist. Must include logo,
Name: Belinda Harwick
Title: Director and Stylist
telephone : +61 8 7142 5809
email: belinda@theloombriefing.example
website: theloombriefing.example
Tag: Corporate Workwear & Uniform Specialist | Personal Stylist
Would like nice icons for telephone, email, website

Target Market(s)

Businesses wanting stylish uniforms, people wanting stylish wardrobes

Industry/Entity Type

Corporate Workwear Stylist

Contact Information for Business Card

I would like black, white and gold foiling incorporated in the design - possibly a touch of the other colours on my branding guide attached Name: Belinda Harwick Title: Director and Stylist telephone : +61 8 7142 5809 email: belinda@theloombriefing.example website: theloombriefing.example Tag: Corporate Workwear & Uniform Specialist | Personal Stylist Would like nice icons for telephone, email, website

Font styles to use
Other font styles liked:
• Raleway

Colors

Designer to choose colors to be used in the design.

Requirements
Must have
• Gold foil accents

```html
<!DOCTYPE html>
<html lang="en">
<head>
<meta charset="utf-8">
<title>The Loom Briefing — Business Cards</title>
<link rel="stylesheet" href="https://fonts.googleapis.com/css2?family=Montserrat:wght@400;500&family=Raleway:wght@400;500;600&display=swap">
<style>
  :root {
    --ink: #1f1d1e;
    --paper: #f6f6f7;
    --gold: #d9ac3a;
    --gold-deep: #b98a22;
    --silver: #dcdcdc;
    --mist: #c9c9c9;
    --stage-top: #e9e9e9;
    --stage-bottom: #bdbdbd;
  }
  * { box-sizing: border-box; margin: 0; padding: 0; }
  html, body { width: 1200px; height: 800px; overflow: hidden; }
  body {
    background: linear-gradient(160deg, var(--stage-top), var(--stage-bottom));
    font-family: "Raleway", sans-serif;
    display: flex;
    align-items: center;
    justify-content: center;
    gap: 40px;
  }
  .card {
    position: relative;
    width: 540px;
    height: 330px;
    background: var(--ink);
    border-bottom: 3px solid var(--gold);
    border-right: 2px solid var(--gold);
    overflow: hidden;
    box-shadow: 0 12px 28px rgba(0,0,0,.25);
  }
  .card-front__wave { position: absolute; inset: 0; width: 100%; height: 100%; }

  .brand-mark {
    position: absolute;
    font-family: "Raleway", sans-serif;
    font-weight: 500;
    text-transform: uppercase;
    line-height: 1.15;
    text-align: center;
  }
  .card-front .brand-mark {
    left: 40px; top: 105px; width: 190px;
    color: var(--silver);
    font-size: 22px;
    letter-spacing: 4px;
  }
  .card-back .brand-mark {
    left: 0; right: 0; top: 100px;
    color: var(--gold);
    font-size: 38px;
    letter-spacing: 7px;
  }

  .contact {
    position: absolute;
    right: 24px; top: 120px;
    text-align: right;
    color: var(--ink);
  }
  .contact__name {
    font-family: "Montserrat", sans-serif;
    font-weight: 500;
    font-size: 18px;
    letter-spacing: .5px;
    text-transform: uppercase;
  }
  .contact__title {
    font-family: "Montserrat", sans-serif;
    color: var(--gold);
    font-size: 12px;
    margin: 2px 0 8px;
  }
  .contact__list { list-style: none; }
  .contact__item {
    display: flex;
    justify-content: flex-end;
    align-items: center;
    gap: 7px;
    font-family: "Montserrat", sans-serif;
    font-size: 11px;
    line-height: 17px;
    color: #333;
  }
  .contact__icon { width: 11px; height: 11px; flex: none; }

  .tagline {
    position: absolute;
    left: 0; right: 0; bottom: 38px;
    text-align: center;
    font-family: "Montserrat", sans-serif;
    font-size: 11px;
    letter-spacing: 1.6px;
    color: var(--mist);
    text-transform: uppercase;
  }
  .tagline__sep { color: var(--gold); padding: 0 4px; }
</style>
</head>
<body>

  <section class="card card-front" aria-label="Business card front">
    <svg class="card-front__wave" viewBox="0 0 540 330" preserveAspectRatio="none" aria-hidden="true">
      <path d="M0 262 C150 250 200 225 240 160 C285 90 380 125 540 120 L540 330 L0 330 Z" fill="var(--gold)"/>
      <path d="M0 268 C155 256 206 232 247 166 C290 98 385 131 540 128 L540 330 L0 330 Z" fill="var(--paper)"/>
    </svg>

    <div class="brand-mark">The Loom<br>Briefing</div>

    <div class="contact">
      <p class="contact__name">Belinda Harwick</p>
      <p class="contact__title">Director &amp; Stylist</p>
      <ul class="contact__list">
        <li class="contact__item">+61 8 7142 5809
          <svg class="contact__icon" viewBox="0 0 12 12" aria-hidden="true"><path d="M2.5 1 L4.5 1 L5 3.5 L3.8 4.5 C4.5 6 6 7.5 7.5 8.2 L8.5 7 L11 7.5 L11 9.5 C11 10.5 10.2 11 9.5 11 C5 10.7 1.3 7 1 2.5 C1 1.8 1.5 1 2.5 1 Z" fill="var(--gold)"/></svg>
        </li>
        <li class="contact__item">belinda@theloombriefing.example
          <svg class="contact__icon" viewBox="0 0 12 12" aria-hidden="true"><rect x="1" y="2.5" width="10" height="7" rx="1" fill="var(--gold)"/><path d="M1.5 3 L6 6.5 L10.5 3" stroke="var(--paper)" stroke-width="1" fill="none"/></svg>
        </li>
        <li class="contact__item">theloombriefing.example
          <svg class="contact__icon" viewBox="0 0 12 12" aria-hidden="true"><circle cx="6" cy="6" r="5.5" fill="var(--gold)"/><path d="M1 6 H11 M6 .5 C3.5 3 3.5 9 6 11.5 M6 .5 C8.5 3 8.5 9 6 11.5" stroke="var(--paper)" stroke-width=".8" fill="none"/></svg>
        </li>
      </ul>
    </div>
  </section>

  <section class="card card-back" aria-label="Business card back">
    <div class="brand-mark">The Loom<br>Briefing</div>
    <p class="tagline">
      Corporate Workwear<span class="tagline__sep">|</span>Uniform Specialist<span class="tagline__sep">|</span>Personal Stylist
    </p>
  </section>

</body>
</html>
```